Quillmont Energy b-card redesign

I would like to redesign the card (and power point template) for quillmont energy. We are a developer/owner/operator of high-tech biomass gasification power plants. We take ag waste like nut shells or fruit pits and convert that into electricity in the 1/2 - 3 MW range. I would like to change our company color from red to golden gate bridge orange (C=0,M=69,,Y=100,B=6).

```html
<!DOCTYPE html>
<html lang="en">
<head>
<meta charset="utf-8">
<title>Quillmont Energy business card</title>
<link href="https://fonts.googleapis.com/css2?family=Roboto+Condensed:wght@400;700&display=swap" rel="stylesheet">
<style>
  :root {
    --bg: #e4e2de;
    --card-white: #ffffff;
    --band-light: #ececec;
    --band-light-edge: #d6d6d6;
    --charcoal: #2b2b2b;
    --charcoal-deep: #1f1f1f;
    --icon-box: #3a3a3a;
    --accent: #f04a00;
    --ink: #333333;
    --ink-soft: #555555;
  }
  * { margin: 0; padding: 0; box-sizing: border-box; }
  html, body { width: 1200px; height: 790px; overflow: hidden; }
  body {
    background: var(--bg);
    font-family: "Roboto Condensed", "Arial Narrow", sans-serif;
    position: relative;
  }
  .card {
    position: absolute;
    width: 540px;
    height: 315px;
    overflow: hidden;
    box-shadow: 0 6px 18px rgba(0,0,0,0.18);
  }
  .card-front {
    left: 40px; top: 150px;
    background: var(--card-white);
    display: flex; align-items: center; justify-content: center;
  }
  .card-back {
    left: 620px; top: 325px;
    background: var(--charcoal);
  }
  .wordmark {
    display: flex; align-items: center; gap: 10px;
    color: var(--ink);
    font-size: 30px;
    font-weight: 400;
    letter-spacing: 1px;
    text-transform: uppercase;
    white-space: nowrap;
  }
  .wordmark .dot {
    width: 12px; height: 12px; border-radius: 50%;
    background: var(--accent);
    flex: none;
  }
  .card-back .wordmark { font-size: 28px; }
  .back-top-band {
    position: absolute; left: 0; top: 0; width: 100%; height: 16px;
    background: var(--charcoal-deep);
  }
  .back-header {
    position: absolute; left: 0; top: 16px; width: 100%; height: 92px;
    background: linear-gradient(180deg, var(--card-white), var(--band-light) 70%, var(--band-light-edge));
    display: flex; align-items: center; justify-content: center;
  }
  .contact-list {
    position: absolute; left: 296px; top: 118px; width: 244px;
    list-style: none;
    display: flex; flex-direction: column; gap: 6px;
  }
  .contact-row {
    display: flex; align-items: center; gap: 8px;
    background: var(--card-white);
    height: 22px;
    padding-left: 4px;
    font-size: 10.5px;
    color: var(--ink);
    white-space: nowrap;
  }
  .contact-row.address { height: 40px; line-height: 1.3; }
  .icon-box {
    width: 16px; height: 16px; flex: none;
    background: var(--icon-box);
    display: flex; align-items: center; justify-content: center;
  }
  .contact-row.address .icon-box { height: 32px; }
  .icon-box svg { width: 10px; height: 10px; fill: var(--accent); }
  .identity {
    position: absolute; left: 78px; top: 212px;
    width: 190px; height: 48px;
    background: linear-gradient(180deg, var(--card-white), var(--band-light));
    padding: 10px 0 0 14px;
  }
  .identity-strip {
    position: absolute; left: 0; top: 240px; width: 78px; height: 20px;
    background: var(--band-light-edge);
  }
  .person-name {
    color: var(--accent);
    font-size: 13px; letter-spacing: 0.8px; text-transform: uppercase;
  }
  .person-role {
    color: var(--ink);
    font-size: 10.5px; letter-spacing: 0.5px; text-transform: uppercase;
  }
</style>
</head>
<body>
  <section class="card card-front">
    <div class="wordmark"><span class="dot"></span>Quillmont Energy</div>
  </section>

  <section class="card card-back">
    <div class="back-top-band"></div>
    <header class="back-header">
      <div class="wordmark"><span class="dot"></span>Quillmont Energy</div>
    </header>

    <ul class="contact-list">
      <li class="contact-row">
        <span class="icon-box"><svg viewBox="0 0 10 10"><path d="M2 0.5h2l0.8 2.2-1.2 0.8a5 5 0 0 0 2.9 2.9l0.8-1.2 2.2 0.8v2a1 1 0 0 1-1 1A8.5 8.5 0 0 1 1 1.5a1 1 0 0 1 1-1z"/></svg></span>
        014 555 0192
      </li>
      <li class="contact-row">
        <span class="icon-box"><svg viewBox="0 0 10 10"><path d="M3 0h4a1 1 0 0 1 1 1v8a1 1 0 0 1-1 1H3a1 1 0 0 1-1-1V1a1 1 0 0 1 1-1zm0 1.5v6h4v-6z"/></svg></span>
        014 555 0193
      </li>
      <li class="contact-row">
        <span class="icon-box"><svg viewBox="0 0 10 10"><path d="M0 2h10v6H0zm1 1v0.3l4 2.4 4-2.4V3z"/></svg></span>
        hello@quillmont.com
      </li>
      <li class="contact-row">
        <span class="icon-box"><svg viewBox="0 0 10 10"><path d="M5 0a5 5 0 1 0 0 10A5 5 0 0 0 5 0zm0 1c.6.7 1 1.8 1.1 3.5H3.9C4 2.8 4.4 1.7 5 1zM1 5.5h2c.1 1.5.4 2.5.9 3.3A4 4 0 0 1 1 5.5zm0-1a4 4 0 0 1 2.9-3.3c-.5.8-.8 1.8-.9 3.3zm5.1 4.3c.5-.8.8-1.8.9-3.3h2a4 4 0 0 1-2.9 3.3zM7 4.5c-.1-1.5-.4-2.5-.9-3.3A4 4 0 0 1 9 4.5zM5 9c-.6-.7-1-1.8-1.1-3.5h2.2C6 7.2 5.6 8.3 5 9z"/></svg></span>
        www.quillmontenergy.com
      </li>
      <li class="contact-row address">
        <span class="icon-box"><svg viewBox="0 0 10 10"><path d="M5 0a3.5 3.5 0 0 1 3.5 3.5C8.5 6 5 10 5 10S1.5 6 1.5 3.5A3.5 3.5 0 0 1 5 0zm0 2a1.5 1.5 0 1 0 0 3 1.5 1.5 0 0 0 0-3z"/></svg></span>
        <span>27 Harlow Street, 4th floor<br>Leeds UK</span>
      </li>
    </ul>

    <div class="identity-strip"></div>
    <div class="identity">
      <p class="person-name">Daniel Marsh</p>
      <p class="person-role">Financial Advisor</p>
    </div>
  </section>
</body>
</html>
```